Vexa - Booking activities for Kids and Adults.

The app allows booking of Kid's activities for a given date/time.
The app lists activities offered via various clubs (vendors) which a user can book for their kids.
The users can browse various clubs and their offered activities. The users can manage their kid's profiles.
Need a whole new look to the app. The existing app can be checked out at
https://apps.storefrontexample.test/details?id=com.vexakw
https://apps.appmarketexample.test/us/app/vexa-فيكسا/id7302958146?ls=1
Try using the app as Guest.

Target Market(s)

Kuwait

Font styles to use
Serif
Sans Serif

Requirements
Must have
• Home Screens
The home page should have everything from the existing app and a quick area to change between different kid's profile to see activities matching their interests ONLY. In the current version, there's no switch profile and hence we are showing the name tags on the activities.

We are also going to build ecommerce so we need that ecommerce look and feel.
Kindly maintain the image aspect ratio from the current app so the new version doesn't require new images.

Need a complete new innovative designs - Keep the color scheme same.
The designs should be minimalistic and image oriented. The design should be done in XD. The designs should be submitted in both light and dark theme.
Reference to be used - http://plimtor.example

D.M for more info if needed.

```html
<!DOCTYPE html>
<html lang="en">
<head>
<meta charset="utf-8">
<title>Vexa – Welcome</title>
<link rel="stylesheet" href="https://fonts.googleapis.com/css2?family=Poppins:wght@400;600;700&family=Patrick+Hand&display=swap">
<style>
  :root {
    --teal: #3dd8d4;
    --teal-light: #5fe3df;
    --teal-deep: #2ccbc7;
    --white: #ffffff;
    --ink: #3a3a3a;
    --orange: #f7941d;
    --orange-shadow: rgba(160, 90, 10, 0.28);
  }
  * { margin: 0; padding: 0; box-sizing: border-box; }
  html, body {
    width: 1200px;
    height: 2588px;
    overflow: hidden;
    background: var(--teal);
  }
  .welcome-screen {
    position: relative;
    width: 1200px;
    height: 2588px;
    overflow: hidden;
    font-family: "Poppins", sans-serif;
  }
  .doodle-backdrop {
    position: absolute;
    inset: 0;
    background: radial-gradient(ellipse at 50% 45%, var(--teal-light) 0%, var(--teal) 55%, var(--teal-deep) 100%);
  }
  .language-switch {
    position: absolute;
    top: 204px;
    left: 908px;
    width: 228px;
    height: 84px;
    border-radius: 42px;
    background: var(--white);
    display: flex;
    align-items: center;
    padding: 0 22px 0 20px;
    gap: 18px;
    box-shadow: 0 4px 12px rgba(0, 0, 0, 0.08);
  }
  .language-switch .flag-dot {
    width: 48px;
    height: 48px;
    border-radius: 50%;
    background: #2b3a8c;
    flex: none;
  }
  .language-switch .language-code {
    font-weight: 600;
    font-size: 34px;
    color: var(--ink);
    flex: 1;
  }
  .language-switch svg { flex: none; }
  .brand {
    position: absolute;
    top: 1170px;
    left: 0;
    width: 1200px;
    text-align: center;
    color: var(--white);
  }
  .brand-name {
    font-family: "Poppins", sans-serif;
    font-weight: 600;
    font-size: 250px;
    line-height: 1;
    letter-spacing: -4px;
  }
  .brand-tagline {
    margin-top: 36px;
    font-family: "Patrick Hand", cursive;
    font-size: 42px;
    letter-spacing: 1px;
  }
  .get-started {
    position: absolute;
    top: 2072px;
    left: 200px;
    width: 800px;
    height: 140px;
    border: none;
    border-radius: 70px;
    background: var(--orange);
    color: var(--white);
    font-family: "Poppins", sans-serif;
    font-weight: 600;
    font-size: 50px;
    letter-spacing: 2px;
    box-shadow: 0 18px 30px var(--orange-shadow);
  }
</style>
</head>
<body>
  <main class="welcome-screen">
    <div class="doodle-backdrop" role="img" aria-label="Light line doodles of playful children, balls, books and stars scattered across the teal background"></div>

    <div class="language-switch">
      <span class="flag-dot"></span>
      <span class="language-code">En</span>
      <svg width="22" height="14" viewBox="0 0 22 14" aria-hidden="true">
        <path d="M2 2 L11 11 L20 2" fill="none" stroke="#3a3a3a" stroke-width="3" stroke-linecap="round" stroke-linejoin="round"/>
      </svg>
    </div>

    <div class="brand">
      <div class="brand-name">Vexa</div>
      <p class="brand-tagline">For Active Bodies &amp; Bright Minds</p>
    </div>

    <button class="get-started" type="button">GET STARTED</button>
  </main>
</body>
</html>
```